Catalogue Design Project

We need a catalog design for a new private university called Redwell Institute Bayshore (see website www.rwi-bs.org). The catalog should be about 30 pages maximum and will include items such as General Information, Academic schedule, department descriptions, program descriptions, course descriptions, school policies, student services, admissions, San diego Lifestyle, etc.
I will provide the text but I need a professional design with regard to page layouts. I have provided some examples.
Ok, i posted the catalog content, just missing course descriptions.
Target Market(s)
Young Professionals, Foreign Students
Industry/Entity Type
University
Look and feel
Each slider illustrates characteristics of the customer's brand and the style your logo design should communicate.

```html
<!DOCTYPE html>
<html lang="en">
<head>
<meta charset="utf-8">
<title>Accounting Certificate – Redwell Institute</title>
<link href="https://fonts.googleapis.com/css2?family=Carlito:wght@400;700&display=swap" rel="stylesheet">
<style>
  :root {
    --ink: #1a1a1a;
    --brand-blue: #2f6597;
    --rule-blue: #6a8fb5;
    --footer-grey: #8c8c8c;
    --paper: #ffffff;
    --parchment: #d9c49c;
    --parchment-light: #f4ecdc;
    --dot-grey: #b9b9b9;
  }
  * { margin: 0; padding: 0; box-sizing: border-box; }
  html, body { width: 927px; height: 1200px; overflow: hidden; background: var(--paper); }
  body { font-family: "Carlito", "Calibri", sans-serif; color: var(--ink); }
  .page { position: relative; width: 927px; height: 1200px; overflow: hidden; }

  .masthead-photo {
    position: absolute; left: 560px; top: 0; width: 367px; height: 103px;
    background: linear-gradient(100deg, rgba(255,255,255,1) 0%, var(--parchment-light) 30%, var(--parchment) 75%, #c9ad7e 100%);
  }
  .masthead-motif {
    position: absolute; left: 58px; top: 38px; width: 156px; height: 38px;
    background: linear-gradient(90deg, var(--brand-blue) 0%, var(--dot-grey) 25%, var(--dot-grey) 80%, var(--brand-blue) 100%);
    border-radius: 19px; opacity: .55;
  }
  .masthead-rule { position: absolute; left: 0; top: 102px; width: 600px; height: 2px; background: var(--rule-blue); }
  .section-band { position: absolute; left: 570px; top: 102px; width: 357px; height: 42px; }
  .section-band__label {
    position: absolute; left: 585px; top: 104px; width: 342px; height: 40px;
    color: #fff; font-size: 30px; line-height: 40px; text-align: center; letter-spacing: .3px;
  }

  .content { position: absolute; left: 80px; top: 200px; width: 803px; }
  .program-title { font-size: 25px; font-weight: 700; text-align: center; line-height: 34px; margin-bottom: 2px; }
  .program-intro p { font-size: 19.6px; line-height: 33.5px; text-align: justify; }
  .program-facts { font-size: 19.6px; line-height: 33.5px; }
  .program-facts strong { font-weight: 700; }

  .course-group { position: absolute; font-size: 19px; line-height: 25.5px; }
  .course-group__heading { text-decoration: underline; }
  .course-group--required { left: 80px; top: 715px; }
  .course-group--elective { left: 76px; top: 826px; width: 800px; }
  .elective-grid { display: grid; grid-template-columns: 381px 381px; }
  .elective-grid__wide { grid-column: 1 / 3; padding-left: 218px; }
  .course-group--outcome { left: 80px; top: 990px; width: 803px; }

  .footer-rule { position: absolute; left: 0; top: 1157px; width: 927px; height: 1.5px; background: var(--rule-blue); opacity: .7; }
  .footer-mark {
    position: absolute; right: 40px; top: 1169px; font-size: 13.5px; color: var(--footer-grey); letter-spacing: .2px;
  }
</style>
</head>
<body>
<div class="page">
  <header>
    <div class="masthead-photo" role="img" aria-label="Faded photograph of an open antique book"></div>
    <div class="masthead-motif" role="img" aria-label="Decorative dot motif in grey and blue"></div>
    <div class="masthead-rule"></div>
    <svg class="section-band" viewBox="0 0 357 42" aria-hidden="true">
      <polygon points="14,0 357,0 357,42 0,42" fill="#2f6597"/>
    </svg>
    <div class="section-band__label">CERTIFICATE PROGRAMS</div>
  </header>

  <main class="content">
    <h1 class="program-title">Accounting Certificate</h1>
    <div class="program-intro">
      <p>According to Career Ledger: “The National Labor Research Office projects 15.7 percent growth for accountants between 2010 and 2020, which is much faster than the average growth for most other professions. An additional 190,700 accounting and auditing jobs will need to be filled during that time period.”</p>
      <p>Redwell Institute realizes this need of nearly all organizations to have on staff a qualified accountant and thus offers a certificate that is ideal for students wanting to pursue the accounting profession, advance their career and increase their earning potential.</p>
      <p>Today's accountant has responsibilities that can include maintenance of all company finances, reporting, record keeping, projections, budgets, and general bookkeeping. To ensure graduates from the Accounting Certificate meet the demands of the organization to which they become employed, the curriculum includes all necessary coursework to arrange a smooth transition from the classroom to the workplace.</p>
    </div>
    <div class="program-facts">
      <div><strong>Hours:</strong> 6 hours per week</div>
      <div><strong>Length:</strong> 8 weeks per course</div>
    </div>
  </main>

  <section class="course-group course-group--required">
    <div class="course-group__heading">Required Courses:</div>
    <div>ACCT 600 Financial Accounting</div>
    <div>ACCT 601 Managerial Accounting</div>
    <div>ACCT 602 Computerized Accounting</div>
  </section>

  <section class="course-group course-group--elective">
    <div class="course-group__heading">Elective Courses: (Choose 2)</div>
    <div class="elective-grid">
      <div>ACCT 603 Federal Taxation</div><div>ACCT 604 Cost Accounting</div>
      <div>ACCT 605 Introduction to Investments</div><div>ACCT 606 Introduction to Auditing</div>
      <div>ACCT 607 Accounting Internship</div><div>ACCT 608 General Bookkeeping</div>
      <div>ACCT 612 Computerized Accounting II</div><div>ACCT 622 Computerized Accounting III</div>
      <div class="elective-grid__wide">BUS 600 Starting Your Own Business</div>
    </div>
  </section>

  <section class="course-group course-group--outcome">
    <div class="course-group__heading">Learning Outcome:</div>
    <div>Gain a well-rounded understanding of practical accounting principles and put them to use in real job projects and tasks.</div>
  </section>

  <footer>
    <div class="footer-rule"></div>
    <div class="footer-mark">8::: REDWELL INSTITUTE</div>
  </footer>
</div>
</body>
</html>
```